Bref créative
Kawamovi business cards/stationary
Relocation Support Services
I need single sided standard sized Business Card [3.5" x 2"]
Designer's discretion
Professional
Ned Fallow
President
4-31-09 Nishikubo
Meguro-ku, Tokyo 158-0271
ned@kawamovi.example
www.kawamovi.example
Have not yet received logo files from designer. I will be using
Will upload Al format as soon as I receive from designer.
Kawamovi logo to be used

```html
<!DOCTYPE html>
<html lang="en">
<head>
<meta charset="utf-8">
<title>Kawamovi — Business Card</title>
<link href="https://fonts.googleapis.com/css2?family=Lato:wght@400;700&display=swap" rel="stylesheet">
<style>
  :root {
    --backdrop: #e9e6e2;
    --card: #ffffff;
    --brand-red: #c8102e;
    --brand-red-dark: #9e0c24;
    --text-dark: #3b3b3b;
    --text-muted: #7d7d7d;
    --divider: #d8d8d8;
  }
  * { box-sizing: border-box; margin: 0; padding: 0; }
  html, body {
    width: 1200px; height: 780px; overflow: hidden;
    background: var(--backdrop);
    font-family: "Lato", "Helvetica Neue", Arial, sans-serif;
  }
  .canvas {
    width: 1200px; height: 780px;
    display: flex; align-items: center; justify-content: center;
  }
  .business-card {
    position: relative;
    width: 1050px; height: 600px;
    background: var(--card);
    border-radius: 34px;
    overflow: hidden;
    box-shadow: 0 10px 30px rgba(0,0,0,0.18);
  }
  .edge-accent {
    position: absolute; left: 0; top: 0;
    width: 70px; height: 600px;
    background: linear-gradient(to bottom, var(--brand-red), var(--brand-red-dark));
  }
  .brand-block {
    position: absolute; left: 150px; top: 250px;
    width: 330px;
    display: flex; flex-direction: column; align-items: center;
  }
  .brand-row { display: flex; align-items: center; gap: 14px; }
  .brand-dot {
    width: 30px; height: 30px; border-radius: 50%;
    background: var(--brand-red);
  }
  .brand-name {
    font-size: 60px; font-weight: 700; color: var(--brand-red);
    letter-spacing: -1px; line-height: 1;
  }
  .brand-tagline {
    margin-top: 8px; align-self: flex-end; margin-right: 10px;
    font-size: 17px; color: var(--text-muted);
  }
  .divider {
    position: absolute; left: 520px; top: 40px;
    width: 2px; height: 520px;
    background: linear-gradient(to bottom, rgba(216,216,216,0), var(--divider) 15%, var(--divider) 85%, rgba(216,216,216,0));
  }
  .contact-block {
    position: absolute; left: 560px; top: 78px;
    color: var(--text-dark);
  }
  .person-name {
    font-size: 32px; font-weight: 700; color: var(--brand-red); line-height: 1.1;
  }
  .person-title {
    font-size: 18px; color: var(--text-muted); margin-top: 4px;
  }
  .address {
    margin-top: 108px; font-size: 19px; line-height: 1.45;
  }
  .contact-list { list-style: none; margin-top: 16px; }
  .contact-item {
    display: flex; align-items: center; gap: 10px;
    font-size: 19px; line-height: 1.55;
  }
  .contact-icon { width: 18px; height: 18px; flex: none; }
</style>
</head>
<body>
<main class="canvas">
  <article class="business-card">
    <div class="edge-accent" role="img" aria-label="Red decorative band along the left edge"></div>

    <div class="brand-block">
      <div class="brand-row">
        <span class="brand-dot"></span>
        <span class="brand-name">Kawamovi</span>
      </div>
      <span class="brand-tagline">Relocation Services</span>
    </div>

    <div class="divider"></div>

    <section class="contact-block">
      <h1 class="person-name">Ned Fallow</h1>
      <p class="person-title">President</p>
      <p class="address">4-31-09 Nishikubo<br>Meguro-ku, Tokyo 158-0271</p>
      <ul class="contact-list">
        <li class="contact-item">
          <svg class="contact-icon" viewBox="0 0 24 24" aria-hidden="true"><path d="M6.6 10.8a15.1 15.1 0 0 0 6.6 6.6l2.2-2.2a1 1 0 0 1 1-.25 11.4 11.4 0 0 0 3.6.57 1 1 0 0 1 1 1V20a1 1 0 0 1-1 1A17 17 0 0 1 3 4a1 1 0 0 1 1-1h3.5a1 1 0 0 1 1 1c0 1.25.2 2.45.57 3.57a1 1 0 0 1-.25 1z" fill="var(--brand-red)"/></svg>
          +81 (0)80-5550-1942
        </li>
        <li class="contact-item">
          <svg class="contact-icon" viewBox="0 0 24 24" aria-hidden="true"><circle cx="12" cy="12" r="11" fill="var(--brand-red)"/><text x="12" y="16.5" font-size="13" font-weight="700" fill="#fff" text-anchor="middle" font-family="Lato, sans-serif">@</text></svg>
          ned@kawamovi.example
        </li>
        <li class="contact-item">
          <svg class="contact-icon" viewBox="0 0 24 24" aria-hidden="true"><circle cx="12" cy="12" r="10" fill="none" stroke="var(--brand-red)" stroke-width="2"/><ellipse cx="12" cy="12" rx="4.5" ry="10" fill="none" stroke="var(--brand-red)" stroke-width="1.6"/><line x1="2" y1="12" x2="22" y2="12" stroke="var(--brand-red)" stroke-width="1.6"/></svg>
          www.kawamovi.example
        </li>
      </ul>
    </section>
  </article>
</main>
</body>
</html>
```